Logo & nopcommerce theme design for a webshop in gadgets & lifestyle products

We are looking for someone who can design a logo and a nopcommerce theme for our webshop. The name of the shop is Lumavorp. The logo should also be used for plaztrove. In the attached file we have an example of a theme that is close what we are looking for. The coloring should be different but the lay-out is ok. Only on the left we want a column to choose a sub category and a column where you can set some filters to search in detail for a product.

Industry/Entity Type

Shop

Number of Pages Required

1 page

Requirements
Must have
• The Nopcommerce theme for 3.40 should have a professional look, not to color full and for the rest we leave it to the designer
Nice to have
• n/a
Should not have
• n/a

```html
<!DOCTYPE html>
<html lang="en">
<head>
<meta charset="utf-8">
<title>Lumavorp – Smartphones &amp; Mobile Phones</title>
<link href="https://fonts.googleapis.com/css2?family=Open+Sans:wght@400;600;700&display=swap" rel="stylesheet">
<style>
:root{
  --red:#d6503f;
  --dark:#3a3b3d;
  --ink:#333;
  --muted:#777;
  --line:#dcdcdc;
  --page:#efefef;
  --panel:#fff;
  --soft:#f4f4f4;
  --badge:#2a6fd0;
}
*{box-sizing:border-box;margin:0;padding:0}
html,body{width:1200px;height:2769px;overflow:hidden}
body{font-family:"Open Sans",Arial,sans-serif;color:var(--ink);background:var(--page);position:relative;font-size:11px}
ul{list-style:none}
.topline{position:absolute;left:0;top:0;width:1200px;height:6px;background:var(--dark)}
.header{position:absolute;left:183px;top:6px;width:834px;height:59px}
.logo{position:absolute;left:0;top:14px;display:flex;align-items:center;gap:8px;font-size:30px;font-weight:700;color:var(--dark);letter-spacing:-.5px}
.logo-mark{width:14px;height:14px;background:var(--red)}
.header-links{position:absolute;left:376px;top:20px;font-size:10px;color:#444;display:flex;align-items:center;gap:5px}
.header-links b{font-weight:600}
.switch{position:absolute;top:12px;display:flex;gap:2px}
.switch span{width:24px;height:30px;display:flex;align-items:center;justify-content:center;font-size:10px;background:#e4e4e4;color:#555}
.switch span.on{background:var(--dark);color:#fff}
.lang{left:623px}.currency{left:710px}
.switch.currency span{width:18px}
.cart{position:absolute;left:777px;top:12px;width:57px;height:32px;background:var(--red);display:flex;align-items:center;justify-content:center}
.nav{position:absolute;left:0;top:65px;width:1200px;height:33px;background:var(--dark)}
.nav ul{position:absolute;left:183px;top:0;display:flex;height:33px}
.nav li{color:#fff;font-size:12px;padding:0 16px;line-height:33px}
.nav li.active{background:var(--red)}
.search{position:absolute;left:786px;top:5px;width:231px;height:24px;background:#fff;font-size:10px;color:#555;padding:5px 8px}
.search svg{position:absolute;right:7px;top:5px}
.categories{position:absolute;left:183px;top:124px;width:279px;height:33px;background:var(--red);color:#fff;font-size:16px;padding:6px 20px;display:flex;justify-content:space-between;align-items:center}
.crumbs{position:absolute;left:476px;top:124px;width:541px;height:33px;background:#ececec;border:1px solid var(--line);font-size:11px;color:#555;display:flex;align-items:center;gap:22px;padding-left:16px}
.tabs{position:absolute;left:183px;top:185px;display:flex;gap:6px}
.tab{height:34px;width:175px;font-size:11px;display:flex;align-items:center;justify-content:center;border:1px solid var(--line);background:#e6e6e6;color:#444}
.tab.on{background:#fff;border-bottom-color:#fff}
.tab .count{color:var(--red)}
.main{position:absolute;left:183px;top:218px;width:834px;height:2200px;background:var(--panel);border:1px solid var(--line)}
.title{position:absolute;left:14px;top:14px;width:805px;font-size:16px;font-weight:400;color:#444;padding-bottom:10px;border-bottom:1px solid var(--line);word-spacing:6px}
.sidebar{position:absolute;left:14px;top:67px;width:174px;height:1038px;background:var(--soft);border:1px solid var(--line)}
.filter h3{font-size:15px;font-weight:400;color:#444;padding:4px 12px 3px;border-bottom:1px solid #ccc;margin:0 0 6px}
.filter li{height:30px;display:flex;align-items:center;gap:14px;padding-left:14px;font-size:10px;color:#444}
.filter li::before{content:"";width:10px;height:10px;border:1px solid #bbb;background:#fff}
.filter{margin-bottom:12px}
.sortbar{position:absolute;left:203px;top:70px;width:616px;height:37px;background:#efefef;border:1px solid var(--line);font-size:10px;color:#444;display:flex;align-items:center;padding:0 10px}
.sortbar .sel{border:1px solid #bbb;background:#fff;width:60px;height:20px;padding:2px 5px;margin:0 10px}
.sortbar u{font-weight:600;margin:0 8px}
.products{position:absolute;left:203px;top:129px;width:618px}
.card{height:164px;margin-bottom:22px;border:1px solid var(--line);position:relative;background:#fff}
.photo{position:absolute;left:12px;top:12px;width:163px;height:137px;border:1px solid #ddd;background:radial-gradient(circle,#cfcfcf 0,#ececec 45%,#f4f4f4 75%)}
.name{position:absolute;left:190px;top:14px;font-size:11px;font-weight:700}
.specs{position:absolute;left:190px;top:38px;font-size:10px;color:#444;line-height:15px}
.specs li::before{content:"•";margin-right:8px}
.rating{position:absolute;left:190px;top:112px;width:214px;height:37px;background:#ececec;border:1px solid #ccc;display:flex;align-items:center;padding-left:6px;gap:3px;font-size:10px}
.star{width:17px;height:17px;background:#fff;display:flex;align-items:center;justify-content:center;font-size:11px;color:#ccc}
.star.on{color:var(--red)}
.rating .score{color:var(--red);font-weight:700;margin-left:5px}
.badge{position:absolute;left:530px;top:16px;width:58px;height:44px;background:var(--badge);border-radius:6px;transform:rotate(-8deg)}
.price{position:absolute;right:17px;top:80px;height:28px;line-height:28px;font-size:24px;font-weight:700;color:var(--red);white-space:nowrap}
.price small{font-size:10px;color:#444;font-weight:400;margin-left:3px}
.btn{position:absolute;left:482px;top:117px;width:118px;height:29px;background:var(--red);color:#fff;font-size:10px;font-weight:700;display:flex;align-items:center;justify-content:center}
.pager{position:absolute;left:354px;top:2121px;display:flex;align-items:center;font-size:10px;color:#444}
.pager span{padding:0 9px;border-left:1px solid #ddd}
.pager .arrow{border:0;font-size:16px;padding:0 28px}
.pager .arrow.next{border-left:1px solid #ddd}
.pager .on{font-weight:700;text-decoration:underline;border:0}
.pager .gap{padding:0 16px}
.showing{position:absolute;left:0;width:834px;top:2165px;text-align:center;font-size:9px;font-style:italic;color:#555}
.footer{position:absolute;left:0;top:2463px;width:1200px;height:236px;background:var(--dark);color:#fff}
.fcol{position:absolute;top:30px;width:188px}
.fcol h4{font-size:15px;font-weight:400;padding-bottom:8px;border-bottom:1px solid #5a5b5e;margin-bottom:16px}
.fcol li{font-size:10px;height:28px;display:flex;gap:12px}
.fcol svg{flex:none}
.bottom{position:absolute;left:183px;top:2699px;width:834px;height:70px;font-size:10px;color:#444}
.bottom .copy{position:absolute;left:0;top:33px}
.social{position:absolute;left:350px;top:30px;display:flex;gap:14px;font-size:11px;font-weight:600;color:var(--dark)}
</style>
</head>
<body>
<div class="topline"></div>
<header class="header">
  <div class="logo"><span>Lumavorp</span><span class="logo-mark"></span></div>
  <div class="header-links">
    <svg width="12" height="12" viewBox="0 0 12 12"><path d="M2 1h3l1 3-2 1a7 7 0 0 0 3 3l1-2 3 1v3c-6 0-10-4-10-9z" fill="#444"/></svg>
    <b>Call us:</b> (0000) 000 0000 • Signup • Sign in •
  </div>
  <div class="switch lang"><span class="on">EN</span><span>FR</span><span>GM</span></div>
  <div class="switch currency"><span class="on">$</span><span>€</span><span>£</span></div>
  <div class="cart"><svg width="18" height="14" viewBox="0 0 18 14"><path d="M1 1h3l2 8h9l2-6H5" fill="none" stroke="#fff" stroke-width="1.5"/><circle cx="7" cy="12" r="1.3" fill="#fff"/><circle cx="14" cy="12" r="1.3" fill="#fff"/></svg></div>
</header>
<nav class="nav">
  <ul><li>Home</li><li class="active">Products</li><li>Register</li><li>Shop</li></ul>
  <div class="search">Search entire store here...<svg width="13" height="13" viewBox="0 0 13 13"><circle cx="5.5" cy="5.5" r="4" fill="none" stroke="#333" stroke-width="1.6"/><path d="M8.5 8.5l3.5 3.5" stroke="#333" stroke-width="1.8"/></svg></div>
</nav>
<div class="categories"><span>Categories</span><svg width="12" height="8" viewBox="0 0 12 8"><path d="M1 1l5 5 5-5" fill="none" stroke="#fff" stroke-width="2"/></svg></div>
<div class="crumbs"><span>Computer</span><span>&gt;</span><span>Smartphones PDAs &amp; Mobiles</span></div>
<div class="tabs"><div class="tab on">All Results&nbsp;<span class="count">(732)</span></div><div class="tab">Special Offers</div></div>

<main class="main">
  <h1 class="title">Smartphones &amp; Mobile Phones</h1>
  <aside class="sidebar">
    <div class="filter"><h3>Thread Count</h3><ul><li>200</li><li>300</li></ul></div>
    <div class="filter"><h3>Bedding Size</h3><ul><li>Single</li><li>Double</li><li>Kingsize</li><li>Super King</li><li>Pillow Case</li></ul></div>
    <div class="filter"><h3>Availability</h3><ul><li>1 Week</li><li>1 Week</li><li>6 Week</li><li>10 Week</li></ul></div>
    <div class="filter"><h3>Colour</h3><ul><li>Blues</li><li>Browns</li><li>Colourful</li><li>Greys</li><li>Metallic</li><li>Neutrals</li><li>Oak</li><li>Patterned</li><li>Purples</li><li>Turquoise</li><li>Whites</li></ul></div>
    <div class="filter"><h3>Price</h3><ul><li>$0 - $ 250</li><li>$250 - $ 500</li><li>$500 - $ 750</li><li>$750 - $ 1000</li><li>$1000 - $ 1250</li></ul></div>
  </aside>
  <div class="sortbar">Sort by price: <u>Low</u> | &nbsp;&nbsp;High<span style="margin-left:auto">Sort By</span><span class="sel">Position</span>Show<span class="sel">Position</span>Per Page</div>

  <div class="products">
    <article class="card"><div class="photo" role="img" aria-label="Product photo: cyan mobile phone"></div><h2 class="name">Norvik 301 Sim Free - Cyan</h2><ul class="specs"><li>2.4" Display</li><li>3.5G connectivity</li><li>100-degree panorama camera function</li><li>Norvik Xpress Browser</li></ul><div class="rating"><span class="star on">★</span><span class="star on">★</span><span class="star on">★</span><span class="star">★</span><span class="star">★</span><span class="score">7.4</span>&nbsp;Read Reviews</div><div class="badge" role="img" aria-label="Free delivery badge"></div><div class="price">$56.99<small>inc. vat</small></div><div class="btn">VIEW PRODUCT</div></article>
    <article class="card"><div class="photo" role="img" aria-label="Product photo: speaker dock"></div><h2 class="name">Fontry Double Bed, Oak</h2><ul class="specs"><li>2.4" Display</li><li>3.5G connectivity</li><li>100-degree panorama camera function</li><li>Norvik Xpress Browser</li></ul><div class="rating"><span class="star on">★</span><span class="star on">★</span><span class="star on">★</span><span class="star">★</span><span class="star">★</span><span class="score">7.4</span>&nbsp;Read Reviews</div><div class="badge" role="img" aria-label="Free delivery badge"></div><div class="price">$56.99<small>inc. vat</small></div><div class="btn">VIEW PRODUCT</div></article>
    <article class="card"><div class="photo" role="img" aria-label="Product photo: tablet"></div><h2 class="name">Fontry Double Bed, Oak</h2><ul class="specs"><li>2.4" Display</li><li>3.5G connectivity</li><li>100-degree panorama camera function</li><li>Norvik Xpress Browser</li></ul><div class="rating"><span class="star on">★</span><span class="star on">★</span><span class="star on">★</span><span class="star">★</span><span class="star">★</span><span class="score">7.4</span>&nbsp;Read Reviews</div><div class="badge" role="img" aria-label="Free delivery badge"></div><div class="price">$56.99<small>inc. vat</small></div><div class="btn">VIEW PRODUCT</div></article>
    <article class="card"><div class="photo" role="img" aria-label="Product photo: smartphones"></div><h2 class="name">Fontry Double Bed, Oak</h2><ul class="specs"><li>2.4" Display</li><li>3.5G connectivity</li><li>100-degree panorama camera function</li><li>Norvik Xpress Browser</li></ul><div class="rating"><span class="star on">★</span><span class="star on">★</span><span class="star on">★</span><span class="star">★</span><span class="star">★</span><span class="score">7.4</span>&nbsp;Read Reviews</div><div class="badge" role="img" aria-label="Free delivery badge"></div><div class="price">$56.99<small>inc. vat</small></div><div class="btn">VIEW PRODUCT</div></article>
    <article class="card"><div class="photo" role="img" aria-label="Product photo: lens camera"></div><h2 class="name">Fontry Double Bed, Oak</h2><ul class="specs"><li>2.4" Display</li><li>3.5G connectivity</li><li>100-degree panorama camera function</li><li>Norvik Xpress Browser</li></ul><div class="rating"><span class="star on">★</span><span class="star on">★</span><span class="star on">★</span><span class="star">★</span><span class="star">★</span><span class="score">7.4</span>&nbsp;Read Reviews</div><div class="badge" role="img" aria-label="Free delivery badge"></div><div class="price">$56.99<small>inc. vat</small></div><div class="btn">VIEW PRODUCT</div></article>
    <article class="card"><div class="photo" role="img" aria-label="Product photo: waffle maker"></div><h2 class="name">Fontry Double Bed, Oak</h2><ul class="specs"><li>2.4" Display</li><li>3.5G connectivity</li><li>100-degree panorama camera function</li><li>Norvik Xpress Browser</li></ul><div class="rating"><span class="star on">★</span><span class="star on">★</span><span class="star on">★</span><span class="star">★</span><span class="star">★</span><span class="score">7.4</span>&nbsp;Read Reviews</div><div class="badge" role="img" aria-label="Free delivery badge"></div><div class="price">$56.99<small>inc. vat</small></div><div class="btn">VIEW PRODUCT</div></article>
    <article class="card"><div class="photo" role="img" aria-label="Product photo: speaker dock"></div><h2 class="name">Fontry Double Bed, Oak</h2><ul class="specs"><li>2.4" Display</li><li>3.5G connectivity</li><li>100-degree panorama camera function</li><li>Norvik Xpress Browser</li></ul><div class="rating"><span class="star on">★</span><span class="star on">★</span><span class="star on">★</span><span class="star">★</span><span class="star">★</span><span class="score">7.4</span>&nbsp;Read Reviews</div><div class="badge" role="img" aria-label="Free delivery badge"></div><div class="price">$56.99<small>inc. vat</small></div><div class="btn">VIEW PRODUCT</div></article>
    <article class="card"><div class="photo" role="img" aria-label="Product photo: tablet"></div><h2 class="name">Fontry Double Bed, Oak</h2><ul class="specs"><li>2.4" Display</li><li>3.5G connectivity</li><li>100-degree panorama camera function</li><li>Norvik Xpress Browser</li></ul><div class="rating"><span class="star on">★</span><span class="star on">★</span><span class="star on">★</span><span class="star">★</span><span class="star">★</span><span class="score">7.4</span>&nbsp;Read Reviews</div><div class="badge" role="img" aria-label="Free delivery badge"></div><div class="price">$56.99<small>inc. vat</small></div><div class="btn">VIEW PRODUCT</div></article>
    <article class="card"><div class="photo" role="img" aria-label="Product photo: smartphones"></div><h2 class="name">Fontry Double Bed, Oak</h2><ul class="specs"><li>2.4" Display</li><li>3.5G connectivity</li><li>100-degree panorama camera function</li><li>Norvik Xpress Browser</li></ul><div class="rating"><span class="star on">★</span><span class="star on">★</span><span class="star on">★</span><span class="star">★</span><span class="star">★</span><span class="score">7.4</span>&nbsp;Read Reviews</div><div class="badge" role="img" aria-label="Free delivery badge"></div><div class="price">$56.99<small>inc. vat</small></div><div class="btn">VIEW PRODUCT</div></article>
    <article class="card"><div class="photo" role="img" aria-label="Product photo: lens camera"></div><h2 class="name">Fontry Double Bed, Oak</h2><ul class="specs"><li>2.4" Display</li><li>3.5G connectivity</li><li>100-degree panorama camera function</li><li>Norvik Xpress Browser</li></ul><div class="rating"><span class="star on">★</span><span class="star on">★</span><span class="star on">★</span><span class="star">★</span><span class="star">★</span><span class="score">7.4</span>&nbsp;Read Reviews</div><div class="badge" role="img" aria-label="Free delivery badge"></div><div class="price">$56.99<small>inc. vat</small></div><div class="btn">VIEW PRODUCT</div></article>
  </div>

  <div class="pager"><span class="arrow">←</span><span class="on">1</span><span>2</span><span>3</span><span>4</span><span>5</span><span class="gap">...</span><span>100</span><span class="arrow next">→</span></div>
  <p class="showing">Displaying 1 to 12 (of 100 products</p>
</main>

<footer class="footer">
  <div class="fcol" style="left:183px"><h4>Contact Us</h4><ul>
    <li><svg width="10" height="12" viewBox="0 0 10 12"><path d="M5 0a4 4 0 0 1 4 4c0 3-4 8-4 8S1 7 1 4a4 4 0 0 1 4-4z" fill="#fff"/><circle cx="5" cy="4" r="1.5" fill="#3a3b3d"/></svg>49 Ardmore, 28 Calderton</li>
    <li><svg width="11" height="11" viewBox="0 0 12 12"><path d="M2 1h3l1 3-2 1a7 7 0 0 0 3 3l1-2 3 1v3c-6 0-10-4-10-9z" fill="#fff"/></svg>+000 (000) 0000</li>
    <li><svg width="11" height="9" viewBox="0 0 11 9"><rect width="11" height="9" fill="#fff"/><path d="M0 0l5.5 5L11 0" fill="none" stroke="#3a3b3d"/></svg>mail@example.com</li></ul></div>
  <div class="fcol" style="left:399px"><h4>Information</h4><ul><li>About Us</li><li>Privacy Policy</li><li>Terms &amp; Conditions</li><li>Secure Payment</li></ul></div>
  <div class="fcol" style="left:613px"><h4>Costumer Service</h4><ul><li>Contact Us</li><li>Return</li><li>FAQ</li><li>Site Map</li></ul></div>
  <div class="fcol" style="left:829px"><h4>My Account</h4><ul><li>My Account</li><li>Order History</li><li>Wish List</li><li>Newsletter</li></ul></div>
</footer>
<div class="bottom">
  <p class="copy">© 2014 Lumavorp. All rights reserved.</p>
  <div class="social"><span>plaztrove</span><span>Chirpline</span><span>Gplexa</span></div>
</div>
</body>
</html>
```